RTavenor Business Cards & Letterhead

I have a logo but need a design for some new business cards. We are a Design-Build Firm that specializes in the design and construction of commercial projects.
the cards need to be professional. no cartoon stuff.
i would like to have the cards in AI format so I can update the card as needed. Logo is provided.
Our Address is: 4187 Marlowe Ct. Apex, North Carolina 27614

```html
<!DOCTYPE html>
<html lang="en">
<head>
<meta charset="UTF-8">
<title>RTavenor Business Card</title>
<link rel="stylesheet" href="https://fonts.googleapis.com/css2?family=Open+Sans:wght@400;600;700;800&display=swap">
<style>
  :root {
    --bg: #1d1e22;
    --blue-deep: #0d3f6e;
    --blue-mid: #1469a8;
    --blue-bright: #1a86d0;
    --grey-logo: #6c6e72;
    --grey-arc: #8a8c90;
    --ink: #222326;
    --white: #ffffff;
  }
  * { box-sizing: border-box; margin: 0; padding: 0; }
  html, body { width: 1200px; height: 780px; overflow: hidden; }
  body {
    background: var(--bg);
    font-family: "Open Sans", Arial, sans-serif;
    position: relative;
  }
  .card {
    position: absolute;
    top: 230px;
    width: 560px;
    height: 320px;
    border-radius: 26px;
    overflow: hidden;
  }
  .card--back {
    left: 25px;
    background: radial-gradient(ellipse at 50% 50%, var(--blue-bright) 0%, var(--blue-mid) 40%, var(--blue-deep) 100%);
    display: flex;
    align-items: center;
    justify-content: center;
  }
  .back-wordmark {
    font-weight: 800;
    font-size: 64px;
    letter-spacing: 2px;
    color: #0f4f86;
  }
  .card--front {
    left: 615px;
    background: var(--white);
  }
  .front-swoosh { position: absolute; inset: 0; }
  .corner-tab {
    position: absolute;
    top: 0; right: 0;
    width: 26px; height: 38px;
    background: var(--blue-mid);
  }
  .person {
    position: absolute;
    top: 20px; right: 40px;
    text-align: right;
  }
  .person-name {
    font-weight: 800;
    font-size: 23px;
    letter-spacing: 0.5px;
    color: var(--blue-bright);
    line-height: 1.1;
  }
  .person-name .surname { color: var(--blue-deep); }
  .person-title {
    font-size: 14px;
    font-weight: 600;
    color: var(--ink);
  }
  .brand {
    position: absolute;
    left: 34px; top: 118px;
    display: flex;
    align-items: center;
    gap: 8px;
  }
  .brand-square {
    width: 24px; height: 24px;
    background: var(--blue-mid);
  }
  .brand-name {
    font-weight: 800;
    font-size: 34px;
    letter-spacing: 1px;
    color: var(--grey-logo);
  }
  .address {
    position: absolute;
    left: 70px; top: 180px;
    font-size: 15px;
    line-height: 1.3;
    color: var(--ink);
  }
  .contacts {
    position: absolute;
    left: 70px; top: 232px;
    list-style: none;
    font-size: 15px;
    line-height: 1.35;
    color: var(--ink);
  }
  .contacts li { display: flex; align-items: center; gap: 8px; }
  .contacts svg { width: 14px; height: 14px; flex: none; }
</style>
</head>
<body>
  <section class="card card--back" aria-label="Card back">
    <span class="back-wordmark">RTAVENOR</span>
  </section>

  <section class="card card--front" aria-label="Card front">
    <svg class="front-swoosh" viewBox="0 0 560 320" preserveAspectRatio="none">
      <defs>
        <linearGradient id="swooshFill" x1="0" y1="1" x2="1" y2="0">
          <stop offset="0" stop-color="#0d3f6e"/>
          <stop offset="0.55" stop-color="#1a7cc4"/>
          <stop offset="1" stop-color="#0f4a80"/>
        </linearGradient>
      </defs>
      <path d="M150,300 C300,292 395,235 425,150" fill="none" stroke="var(--grey-arc)" stroke-width="9"/>
      <path d="M175,320 C330,310 420,240 445,140 C462,80 500,62 560,58 L560,320 Z" fill="url(#swooshFill)"/>
      <path d="M168,312 C325,302 412,236 438,140" fill="none" stroke="#ffffff" stroke-width="4"/>
    </svg>
    <div class="corner-tab"></div>

    <header class="person">
      <p class="person-name">MARCUS <span class="surname">TAVENOR</span></p>
      <p class="person-title">Founder/President</p>
    </header>

    <div class="brand">
      <span class="brand-square"></span>
      <span class="brand-name">RTAVENOR</span>
    </div>

    <address class="address" style="font-style:normal">
      4187 Marlowe Ct. Apex,<br>
      North Carolina 27614
    </address>

    <ul class="contacts">
      <li>
        <svg viewBox="0 0 14 14"><circle cx="7" cy="7" r="7" fill="var(--blue-mid)"/><path d="M4.5,3.5 L6,3.5 L6.6,5.2 L5.7,5.9 C6.2,7 7,7.8 8.1,8.3 L8.8,7.4 L10.5,8 L10.5,9.5 C7,9.8 4.2,7 4.5,3.5 Z" fill="#fff"/></svg>
        (919) 555-0148
      </li>
      <li>
        <svg viewBox="0 0 14 14"><circle cx="7" cy="7" r="7" fill="var(--blue-mid)"/><ellipse cx="7" cy="7" rx="2.3" ry="5" fill="none" stroke="#fff" stroke-width="0.9"/><path d="M2,7 H12" stroke="#fff" stroke-width="0.9"/></svg>
        www.rtavenor.com
      </li>
      <li>
        <svg viewBox="0 0 14 14"><circle cx="7" cy="7" r="7" fill="var(--blue-mid)"/><rect x="3.3" y="4.5" width="7.4" height="5" fill="none" stroke="#fff" stroke-width="0.9"/><path d="M3.3,4.5 L7,7.5 L10.7,4.5" fill="none" stroke="#fff" stroke-width="0.9"/></svg>
        MRT@RTavenor.com
      </li>
    </ul>
  </section>
</body>
</html>
```